Stylish Business Cards Wanted

- DOUBLE SIDED Design Required -

High end, edgy cards for a corporate and personal stylist. Must include logo,
Name: Belinda Harwick
Title: Director and Stylist
telephone : +61 8 7142 5809
email: belinda@theloombriefing.example
website: theloombriefing.example
Tag: Corporate Workwear & Uniform Specialist | Personal Stylist
Would like nice icons for telephone, email, website

Target Market(s)

Businesses wanting stylish uniforms, people wanting stylish wardrobes

Industry/Entity Type

Corporate Workwear Stylist

Contact Information for Business Card

I would like black, white and gold foiling incorporated in the design - possibly a touch of the other colours on my branding guide attached Name: Belinda Harwick Title: Director and Stylist telephone : +61 8 7142 5809 email: belinda@theloombriefing.example website: theloombriefing.example Tag: Corporate Workwear & Uniform Specialist | Personal Stylist Would like nice icons for telephone, email, website

Font styles to use
Other font styles liked:
• Raleway

Colors

Designer to choose colors to be used in the design.

Requirements
Must have
• Gold foil accents

```html
<!DOCTYPE html>
<html lang="en">
<head>
<meta charset="utf-8">
<title>The Loom Briefing – Business Cards</title>
<link rel="stylesheet" href="https://fonts.googleapis.com/css2?family=Roboto:wght@400;500&family=Courgette&display=swap">
<style>
  :root {
    --backdrop: #3a3a3c;
    --card: #1f1f21;
    --gold: #d9b24a;
    --gold-band: #e2bd5c;
    --pink: #e0137a;
    --white: #ffffff;
    --ink: #262626;
  }
  * { box-sizing: border-box; margin: 0; padding: 0; }
  html, body {
    width: 799px; height: 1200px; overflow: hidden;
    background: var(--backdrop);
    font-family: "Roboto", Arial, sans-serif;
  }
  .sheet {
    position: relative; width: 799px; height: 1200px;
    display: flex; flex-direction: column; align-items: center; justify-content: space-around;
    padding: 60px 0;
  }
  .card {
    position: relative; width: 640px; height: 366px;
    background: var(--card); border-radius: 22px; overflow: hidden;
    box-shadow: 0 14px 30px rgba(0,0,0,0.45);
  }
  /* Front */
  .card-front { display: flex; align-items: center; justify-content: center; }
  .brand-name {
    font-family: "Roboto", Arial, sans-serif; font-weight: 500;
    font-size: 54px; letter-spacing: 2px; color: var(--gold);
    display: flex; align-items: center; gap: 18px;
  }
  .brand-mark { width: 22px; height: 22px; background: var(--gold); }
  /* Back */
  .contact { position: absolute; left: 44px; top: 48px; }
  .holder-name {
    font-family: "Courgette", cursive; font-size: 26px; color: var(--gold);
  }
  .holder-title { color: var(--white); font-size: 14px; margin-top: 4px; }
  .details { list-style: none; margin-top: 18px; }
  .details li {
    display: flex; align-items: center; gap: 12px;
    color: var(--white); font-size: 15px; line-height: 25px;
  }
  .details svg { width: 14px; height: 14px; flex: none; }
  .brand-name-small {
    position: absolute; right: 40px; top: 190px;
    font-weight: 500; font-size: 30px; letter-spacing: 1px; color: var(--white);
  }
  .tag-band { position: absolute; left: 0; bottom: 0; width: 640px; height: 72px; }
  .tagline {
    position: absolute; left: 78px; right: 40px; bottom: 18px;
    display: flex; justify-content: space-between;
    color: var(--ink); font-size: 16px;
  }
</style>
</head>
<body>
<main class="sheet">
  <section class="card card-front" aria-label="Card front">
    <div class="brand-name"><span class="brand-mark"></span>The Loom Briefing</div>
  </section>

  <section class="card card-back" aria-label="Card back">
    <div class="contact">
      <p class="holder-name">Belinda Harwick</p>
      <p class="holder-title">Director and Stylist</p>
      <ul class="details">
        <li>
          <svg viewBox="0 0 16 16" fill="none" stroke="var(--gold)" stroke-width="1.4"><circle cx="8" cy="8" r="7"/><path d="M5.5 4.5l1.3 1.6-.8 1c.6 1.2 1.5 2.1 2.7 2.7l1-.8 1.6 1.3-.9 1.2c-2.8-.4-5-2.6-5.4-5.4z" fill="var(--gold)" stroke="none"/></svg>
          +61 8 7142 5809
        </li>
        <li>
          <svg viewBox="0 0 16 16" fill="none" stroke="var(--gold)" stroke-width="1.4"><rect x="1" y="3.5" width="14" height="9" rx="1"/><path d="M1.5 4l6.5 5 6.5-5"/></svg>
          belinda@theloombriefing.example
        </li>
        <li>
          <svg viewBox="0 0 16 16" fill="none" stroke="var(--gold)" stroke-width="1.3"><circle cx="8" cy="8" r="7"/><ellipse cx="8" cy="8" rx="3" ry="7"/><path d="M1 8h14M2.5 4.5h11M2.5 11.5h11"/></svg>
          www.theloombriefing.example
        </li>
      </ul>
    </div>
    <div class="brand-name-small">The Loom Briefing</div>

    <svg class="tag-band" viewBox="0 0 640 72" aria-hidden="true">
      <rect x="0" y="56" width="70" height="16" fill="var(--pink)"/>
      <rect x="600" y="62" width="40" height="10" fill="var(--pink)"/>
      <path d="M62 72 V30 Q62 14 80 14 H588 Q600 14 604 26 L616 72 Z" fill="var(--gold-band)"/>
    </svg>
    <div class="tagline">
      <span>Corporate Workwear &amp; Uniform Specialist</span>
      <span>|</span>
      <span>Personal Stylist</span>
    </div>
  </section>
</main>
</body>
</html>
```